Lottery Website Design

Full website design, where you can take part on a lottery. Inkl Logo. The website is already developed: http://www.zorbel-ziehung.de
I like the modern fullscreen design from
http://www.marvestaplay.com/en-us/home.html
but the field for using the lottery right away should be present as well an the first screen like here:
https://www.glueckspfade.de/spiel/
Colour Scheme:
Red and Yellow?
Responsive design and coding (HTML & CSS).
The current website layout with bootstrap design ist http://www.zorbel-ziehung.de - the logo may be similar to favicon
Feel free to ask! :)
As always I am looking forward for your great ideas!
Updates
Reason: Not yet the best result found ...

```html
<!DOCTYPE html>
<html lang="de">
<head>
<meta charset="utf-8">
<title>Zorbel Ziehung – Kostenlose Lotto-Simulation</title>
<link href="https://fonts.googleapis.com/css2?family=Vollkorn:wght@400;600;700&family=Source+Sans+3:wght@400;600;700&display=swap" rel="stylesheet">
<style>
:root{
  --red:#d0111b;
  --ribbon:#ef5a32;
  --ribbon-dark:#c8401f;
  --yellow:#f9a620;
  --orange:#fd9a35;
  --sky-top:#7cc3ec;
  --sky-bottom:#d9eef9;
  --paper:#efefef;
  --ink:#3a3a3a;
  --muted:#666;
  --grid:#e3e3e3;
  --white:#fff;
}
*{margin:0;padding:0;box-sizing:border-box}
html,body{width:908px;height:1200px;overflow:hidden}
body{position:relative;background:var(--paper);font-family:"Source Sans 3",sans-serif;color:var(--ink)}
.abs{position:absolute}

/* hero */
.hero{left:0;top:0;width:908px;height:448px;background:linear-gradient(180deg,var(--sky-top) 0%,#a9d8f2 55%,var(--sky-bottom) 100%);border-bottom:1px solid #d8d8d8;overflow:hidden}
.ribbon-tail{top:38px;width:52px;height:38px;background:var(--ribbon-dark)}
.ribbon-tail.left{left:38px;clip-path:polygon(0 0,100% 0,100% 100%,0 100%,30% 50%)}
.ribbon-tail.right{left:818px;clip-path:polygon(0 0,100% 0,70% 50%,100% 100%,0 100%)}
.ribbon-bar{left:85px;top:34px;width:739px;height:36px;background:var(--ribbon);box-shadow:0 2px 3px rgba(0,0,0,.2)}
.nav a{position:absolute;top:13px;font-size:10.5px;color:var(--white);text-decoration:none;letter-spacing:.3px;text-transform:uppercase}
.brand{left:410px;top:10px;width:88px;height:88px;border-radius:50%;background:var(--yellow);display:flex;align-items:center;justify-content:center;text-align:center;color:var(--white);font-weight:700;font-size:13px;line-height:1.15}
.share{top:12px;height:14px;padding:0 6px;background:var(--white);border-radius:2px;font-size:9px;line-height:14px;color:#3b6aa8;font-weight:600}
.tagline{left:333px;top:106px;width:241px;height:22px;background:var(--yellow);color:var(--white);font-weight:700;font-size:10.5px;line-height:22px;text-align:center}
.hero-art{left:92px;top:120px;width:304px;height:280px;border-radius:40%;background:radial-gradient(circle,#8fcf6a 0%,#b6dca0 55%,rgba(182,220,160,0) 72%)}
.jackpot-num{left:528px;top:162px;font-family:"Vollkorn",serif;font-weight:700;font-size:84px;color:var(--red);line-height:1}
.jackpot-title{left:595px;top:176px;font-family:"Vollkorn",serif;font-weight:600;font-size:27px;line-height:37px;color:var(--red)}
.hero-copy{left:470px;top:272px;width:334px;text-align:right;font-size:10.5px;line-height:18px;color:#555}
.btn-buy{left:690px;top:329px;width:112px;height:33px;background:linear-gradient(#fdb230,#f7921e);border:1px solid #e58614;color:#b2261a;font-family:"Vollkorn",serif;font-weight:700;font-size:12px;line-height:31px;text-align:center}
.dot{top:421px;width:11px;height:11px;border-radius:50%;background:#9ccbe4}
.dot.on{background:var(--yellow)}

/* step */
.step-title{left:0;top:486px;width:908px;text-align:center;font-family:"Vollkorn",serif;font-size:19px;line-height:28px;color:var(--red)}
.play-panel{left:98px;top:556px;width:712px;height:300px;background:linear-gradient(180deg,#fcaa2a,var(--orange))}
.balls{top:0;height:52px;background:linear-gradient(90deg,rgba(255,255,255,.55),rgba(255,255,255,.15))}
.tickets{left:11px;top:50px;width:525px;height:184px;background:var(--white)}
.field{width:78px;height:78px;background-color:#fafafa;background-image:linear-gradient(var(--grid) 1px,transparent 1px),linear-gradient(90deg,var(--grid) 1px,transparent 1px);background-size:11.14px 11.14px;border:1px solid var(--grid);font-family:"Vollkorn",serif;font-size:56px;line-height:76px;text-align:center;color:#cfcfcf}
.side{left:547px;top:50px;width:153px;height:184px;background:#f3f3f3;padding:0 0 0 12px;font-size:9px;color:#444}
.side p{position:absolute;left:12px}
.digits{left:12px;top:34px;display:flex;gap:2px}
.digit{width:15px;height:15px;background:#e4e4e4;font-weight:700;font-size:10px;text-align:center;line-height:15px}
.digit.super{background:#222;color:var(--white)}
.opt{display:inline-block;padding:0 3px}
.opt.sel{background:var(--white)}
.panel-note{left:16px;top:250px;width:680px;font-size:10.5px;line-height:19px;color:var(--white);font-weight:600}

/* about */
.about-title{left:101px;top:900px;font-family:"Vollkorn",serif;font-size:18px;color:#333}
.about-copy{left:101px;top:942px;width:710px;font-size:10.5px;line-height:18.3px;color:var(--muted)}
.btn-learn{left:102px;top:1029px;width:101px;height:31px;background:var(--yellow);font-family:"Vollkorn",serif;font-size:11.5px;line-height:31px;text-align:center;color:#333}

/* footer */
.footer{left:0;top:1102px;width:908px;height:98px;background:var(--white);border-top:1px solid #ddd}
.social{top:35px;width:21px;height:21px;border-radius:50%;border:1px solid #ccc;background:#f6f6f6}
.copyright{left:100px;top:69px;font-size:9px;color:#777;letter-spacing:.2px}
.to-top{left:764px;top:31px;width:44px;height:43px;background:#f1f1f1;text-align:center;font-size:9.5px;color:#888;padding-top:8px}
</style>
</head>
<body>

<header class="hero abs">
  <div class="ribbon-tail left abs"></div>
  <div class="ribbon-tail right abs"></div>
  <nav class="ribbon-bar nav abs">
    <a href="#" style="left:30px">Infos</a>
    <a href="#" style="left:97px">Startseite</a>
    <a href="#" style="left:187px">Impressum</a>
    <span class="share abs" style="left:584px">Tweet</span>
    <span class="share abs" style="left:637px">Like</span>
  </nav>
  <div class="brand abs">ZORBEL<br>ZIEHUNG</div>
  <div class="tagline abs">Kostenlose Lotto-Simulation mit Kostenkontrolle</div>
  <div class="hero-art abs" role="img" aria-label="Illustration: jubelnder Gewinner in einem Haufen Geldscheine"></div>
  <div class="jackpot-num abs">4</div>
  <h1 class="jackpot-title abs">Millionen Euro<br>im Lotto Jackpot</h1>
  <p class="hero-copy abs">Neque porro quisquam est qui dolorem ipsum quia dolor sit amet, consectetur, adipisci velitNeque porro quisquam dolorem</p>
  <a class="btn-buy abs">BUY NOW</a>
  <span class="dot on abs" style="left:423px"></span>
  <span class="dot abs" style="left:439px"></span>
  <span class="dot abs" style="left:456px"></span>
  <span class="dot abs" style="left:472px"></span>
</header>

<h2 class="step-title abs">.Schritt: Zahlen wählen, die kostenlos bei der nächsten<br>Ziehung geprüft werden sollen</h2>

<section class="play-panel abs">
  <div class="balls abs" style="left:30px;width:110px" role="img" aria-label="Dekorative Lottokugeln"></div>
  <div class="balls abs" style="left:430px;width:282px" role="img" aria-label="Dekorative Lottokugeln"></div>
  <div class="tickets abs">
    <div class="field abs" style="left:10px;top:10px">1</div>
    <div class="field abs" style="left:96px;top:10px">2</div>
    <div class="field abs" style="left:181px;top:10px">3</div>
    <div class="field abs" style="left:267px;top:10px">4</div>
    <div class="field abs" style="left:352px;top:10px">5</div>
    <div class="field abs" style="left:438px;top:10px">6</div>
    <div class="field abs" style="left:10px;top:96px">7</div>
    <div class="field abs" style="left:96px;top:96px">8</div>
    <div class="field abs" style="left:181px;top:96px">9</div>
    <div class="field abs" style="left:267px;top:96px">10</div>
    <div class="field abs" style="left:352px;top:96px">11</div>
    <div class="field abs" style="left:438px;top:96px">12</div>
  </div>
  <aside class="side abs">
    <p style="top:17px;font-family:'Vollkorn',serif;font-weight:700;font-size:8.5px">Losnummer <span style="font-weight:400;color:#888;margin-left:18px;font-family:'Source Sans 3',sans-serif;font-size:7px">Superzahl</span></p>
    <div class="digits abs">
      <span class="digit">2</span><span class="digit">9</span><span class="digit">7</span><span class="digit">5</span><span class="digit">0</span><span class="digit">6</span><span class="digit super">0</span>
    </div>
    <p style="top:69px;line-height:13px">Nächste Ziehung am Samstag,<br>den 19.07.2014</p>
    <p style="top:103px">Spieltage: <span class="opt">Mi</span> <span class="opt sel">Sa</span> <span class="opt">Mi+Sa</span></p>
    <p style="top:132px">Laufzeit in Wochen: <span class="opt sel">1</span> 2 3 4 5</p>
    <p style="top:161px">Warum sind Felder aus gegraut?</p>
  </aside>
  <p class="panel-note abs">Würden Sie mit den Zahlen tatsächlich Lotto spielen (was mit Zorbel-Ziehung.de nicht geht - hier ist alles kostenlos simuliert), wäre das ein Gesamtbetrag in Höhe von: 4.10 €</p>
</section>

<h3 class="about-title abs">Warum Zorbel Ziehung?</h3>
<p class="about-copy abs">Jede Woche am Mittwoch und am Samstag werden die Lottozahlen gezogen. Durchschnittlich 21 Millionen Deutsche warten dann darauf, dass genau ihre Zahlen von der Lottofee gezogen werden. Dennoch ist die Chance auf einen Gewinn nur 1:140 Millionen. Ein Sechser mit Superzahl ist unwahrscheinlicher als vom Blitz getroffen zu werden. Selbst ein Gewinn, der gerade einmal den Einsatz des Spiels wieder einbringt, hat eine Chance von nicht einmal zwei Prozent.Trotzdem holen sich Millionen von Menschen Lottoscheine und träumen vom großen Jackpot.</p>
<a class="btn-learn abs">Learn More</a>

<footer class="footer abs">
  <span class="social abs" style="left:100px"></span>
  <span class="social abs" style="left:125px"></span>
  <span class="social abs" style="left:150px"></span>
  <span class="social abs" style="left:175px"></span>
  <p class="copyright abs">COPYRIGHT 2014 ZORBEL-ZIEHUNG.DE</p>
  <a class="to-top abs"><svg width="8" height="6" viewBox="0 0 8 6"><path d="M1 5 L4 2 L7 5" fill="none" stroke="#888" stroke-width="1.5"/></svg><br>Top</a>
</footer>

</body>
</html>
```